Environmental Consultancey needs Web Design

A consultancey firm based in Papua New Guinea specialising servicing a client market primarily in Melanesia, the wider Pacific Region and South East Asia. The firm provides services to community development and resource extraction activites that incorporate sustainable livelihoods for local customary land owners with environmentally responsibile practices and a focus on maintaining biodiversity and ecosystem services. We aim to encompass Culture, Custom and Science in our approach. Our website preferentially will convey a relaxed Pacific Island feel in its colours and design rather than a sterile corporate feel. See attached logo that will need to be visible on page or which may provide basis for ideas for the page.

Target Market(s)

Our target market is primarily the oil, gas and mining industry, secondarily international donor and aid programs followed by government projects and not for profit programs. Services include:
1. Biodiversity and Conservation - Fauna and Flora survey, assessment, management, monitoring & research, protected areas & endangered & threatend species.
2. Social & Community - impact, stakeholder engagement, census and survey, land and community affairs, capacity building empowerment.
3. Environmental Management - sustainable use, enterprise development & management, biodiversity offsets.

Industry/Entity Type

Community

Requirements
Must have
• Multiple pages, Logo somewhere on home page. Space for a couple of photos that as yet ive not decieded upon.
Nice to have
• Perhaps incorporate shapes, texture and colours that convey a feel of the attached photo of a blue bird of paradise. The blue fine overlapping and interlocking feather patterns are appealing perhaps as a background and the other colours used in boarders ? Abstract is fine as would be symbolic images or tribal ambience. The company is all about blending humanity in all its forms with the environment.

```html
<!DOCTYPE html>
<html lang="en">
<head>
<meta charset="utf-8">
<title>Reefline Ecology</title>
<link rel="stylesheet" href="https://fonts.googleapis.com/css2?family=Cabin:wght@400;500;600&family=Open+Sans:wght@400;700&family=Ubuntu:wght@400;500&family=Oswald:wght@500&display=swap">
<style>
:root{
  --header-bg:#f4f4f4;
  --nav-top:#1570ad;
  --nav-bottom:#04457a;
  --nav-active:#033560;
  --heading-blue:#0b4c7a;
  --body-text:#4a4a4a;
  --panel-top:#ececec;
  --panel-bottom:#d0d0d0;
  --slider-bg:#dadada;
  --accent-orange:#c8552a;
  --accent-cyan:#1aa6d6;
  --footer-bg:#1b1b1b;
  --footer-head:#cfcfcf;
  --footer-text:#a8a8a8;
  --field-bg:#cacaca;
}
*{margin:0;padding:0;box-sizing:border-box}
html,body{width:1050px;height:1200px;overflow:hidden;background:#fff}
body{position:relative;font-family:"Cabin",sans-serif;color:var(--body-text)}
.abs{position:absolute}

.site-header{left:0;top:0;width:1050px;height:188px;background:var(--header-bg);border-bottom:1px solid #dcdcdc}
.brand{left:92px;top:62px;display:flex;align-items:center;gap:10px}
.brand-mark{width:34px;height:34px;border-radius:50%;background:var(--accent-cyan)}
.brand-name{font-family:"Cabin",sans-serif;font-weight:500;font-size:19px;color:var(--heading-blue)}
.header-decor{left:780px;top:0;width:220px;height:160px;background:radial-gradient(ellipse at 45% 50%,#c9d6e6 0%,#e3e8ee 45%,rgba(244,244,244,0) 75%)}

.main-nav{left:50px;top:163px;width:950px;height:48px;border-radius:5px 5px 0 0;background:linear-gradient(var(--nav-top),var(--nav-bottom));border:1px solid #033a66}
.nav-link{top:0;height:46px;line-height:46px;font-family:"Open Sans",sans-serif;font-weight:700;font-size:12.5px;color:#fff;white-space:nowrap}
.nav-link.is-active{background:linear-gradient(#02294b,var(--nav-active));width:72px;text-align:center}
.search{left:750px;top:11px;width:183px;height:24px;border-radius:12px;background:#fff;font-family:"Open Sans",sans-serif;font-style:italic;font-size:12px;color:#555;line-height:24px;padding-left:17px}
.search svg{position:absolute;right:9px;top:4px}

.slider{left:50px;top:211px;width:949px;height:304px;background:var(--slider-bg)}
.slider-shadow{left:130px;top:462px;width:780px;height:40px;border-radius:50%;background:radial-gradient(ellipse,rgba(0,0,0,.35),rgba(0,0,0,0) 70%)}
.slide-arrow{width:34px;height:38px;border-radius:50%;background:radial-gradient(circle at 40% 30%,#5fd1f2,var(--accent-cyan) 60%,#0c7fa8);box-shadow:0 3px 4px rgba(0,0,0,.35)}
.slide-frame{left:114px;top:227px;width:816px;height:250px;background:#fff}
.slide-photo{left:121px;top:235px;width:795px;height:236px;background:linear-gradient(100deg,#4fa7e6 0%,#c6b39b 18%,#d8c6ad 40%,#2e5fc4 52%,#b8763f 62%,#cdb99d 80%,#a99377 100%)}
.slide-caption{left:121px;top:257px;width:795px;height:34px;background:rgba(255,255,255,.62);text-align:right;padding-right:22px;font-family:"Cabin",sans-serif;font-size:21px;line-height:34px;color:#222}
.dot{top:488px;width:13px;height:13px;border-radius:50%;background:radial-gradient(circle at 40% 35%,#777,#222);border:1px solid #111}
.dot.is-current{background:radial-gradient(circle at 40% 35%,#5fb4ee,#0b5fa6)}

.content{left:50px;top:515px;width:949px;height:431px;background:linear-gradient(var(--panel-top),var(--panel-bottom));border-top:1px solid #f6f6f6}
.section-title{font-family:"Cabin",sans-serif;font-weight:500;color:var(--heading-blue);white-space:nowrap}
.welcome-text{left:82px;top:578px;width:606px;font-size:11.5px;line-height:24px;text-align:justify;hyphens:auto;-webkit-hyphens:auto}
.news-date{font-size:13.5px;color:#333}
.news-text{width:246px;font-size:11.5px;line-height:24px;text-align:justify;hyphens:auto;-webkit-hyphens:auto}
.news-rule{left:730px;top:653px;width:240px;height:1px;background:#bcbcbc}

.project-card{top:766px;width:177px;height:158px;border:1px solid #bdbdbd;background:repeating-linear-gradient(135deg,#f4f4f4 0 2px,#e6e6e6 2px 4px);box-shadow:0 1px 2px rgba(0,0,0,.15)}
.project-photo{position:absolute;left:11px;top:9px;width:153px;height:89px}
.project-title{position:absolute;left:11px;top:101px;font-family:"Oswald",sans-serif;font-weight:500;font-size:10.5px;color:var(--accent-orange)}
.project-text{position:absolute;left:11px;top:118px;width:155px;font-family:"Open Sans",sans-serif;font-size:6px;line-height:7.5px;color:#555}
.round-arrow{width:30px;height:30px;border-radius:50%;background:var(--accent-orange);box-shadow:0 1px 2px rgba(0,0,0,.3)}
.round-arrow svg{display:block}

.site-footer{left:0;top:946px;width:1050px;height:254px;background:var(--footer-bg)}
.footer-title{font-family:"Ubuntu",sans-serif;font-weight:500;font-size:20px;color:var(--footer-head);text-shadow:0 2px 2px #000;white-space:nowrap}
.footer-text{left:53px;top:1022px;width:254px;font-family:"Ubuntu",sans-serif;font-size:12.5px;line-height:20px;color:var(--footer-text)}
.footer-links{left:392px;top:1021px;list-style:none;font-family:"Ubuntu",sans-serif;font-size:12.5px;line-height:24px;color:#bdbdbd}
.social{width:35px;height:35px;border-radius:7px;background:#050505;border:1px solid #3a3a3a}
.social svg{display:block;margin:8px auto 0}
.field{left:723px;width:252px;background:var(--field-bg);border:1px solid #000;outline:1px solid #444;font-family:"Ubuntu",sans-serif;font-size:12px;color:#333;padding:2px 9px}
.submit{left:723px;top:1145px;width:87px;height:28px;border-radius:14px;border:3px solid #000;background:linear-gradient(#b5b5b5,#7e7e7e);font-family:"Ubuntu",sans-serif;font-weight:500;font-size:13px;color:#222;text-align:center;line-height:22px}
</style>
</head>
<body>

<header class="site-header abs">
  <div class="brand abs"><span class="brand-mark"></span><span class="brand-name">Reefline Ecology</span></div>
  <div class="header-decor abs" role="img" aria-label="Faint drawing of a bird perched on a branch"></div>
</header>

<nav class="main-nav abs">
  <span class="nav-link abs" style="left:18px">Home</span>
  <span class="nav-link is-active abs" style="left:72px">About us</span>
  <span class="nav-link abs" style="left:175px">Services</span>
  <span class="nav-link abs" style="left:280px">Latest News</span>
  <span class="nav-link abs" style="left:402px">Links</span>
  <span class="nav-link abs" style="left:477px">Contact us</span>
  <div class="search abs">Search
    <svg width="16" height="16" viewBox="0 0 16 16"><circle cx="6.5" cy="6.5" r="4.5" fill="none" stroke="#999" stroke-width="1.6"/><line x1="10" y1="10" x2="14.5" y2="14.5" stroke="#999" stroke-width="2.2" stroke-linecap="round"/></svg>
  </div>
</nav>

<section class="slider abs"></section>
<div class="slider-shadow abs"></div>
<div class="slide-arrow abs" style="left:82px;top:422px"></div>
<svg class="abs" style="left:93px;top:433px" width="12" height="16" viewBox="0 0 12 16"><path d="M9 2 3 8l6 6" fill="none" stroke="#0b2a3a" stroke-width="3"/></svg>
<div class="slide-arrow abs" style="left:928px;top:422px"></div>
<svg class="abs" style="left:938px;top:433px" width="12" height="16" viewBox="0 0 12 16"><path d="M3 2l6 6-6 6" fill="none" stroke="#0b2a3a" stroke-width="3"/></svg>
<div class="slide-frame abs"></div>
<div class="slide-photo abs" role="img" aria-label="Photo of a blue bird diving from a branch"></div>
<div class="slide-caption abs">Encompassing Culture, Custom &amp; Science</div>
<span class="dot abs" style="left:463px"></span>
<span class="dot is-current abs" style="left:485px"></span>
<span class="dot abs" style="left:507px"></span>
<span class="dot abs" style="left:529px"></span>

<main class="content abs"></main>
<h1 class="section-title abs" style="left:80px;top:538px;font-size:25px">Welcome To Reefline Ecology</h1>
<p class="welcome-text abs">Lorem Ipsum is simply dummy text of the printing and typesetting industry. Lorem Ipsum has been the industry's standard dummy text ever since the 1500s, when an unknown printer took a galley of type and scrambled it to make a type specimen book. It has survived not only five centuries, but also the leap into electronic typesetting, remaining essentially unchanged. It was popularised in the 1960s with the release of Quillmere sheets containing Lorem Ipsum passages, and more recently with desktop publishing software like Pressmark Layout including versions of Lorem Ipsum.</p>

<h2 class="section-title abs" style="left:726px;top:534px;font-size:25px">Latest News</h2>
<p class="news-date abs" style="left:730px;top:575px">29, Feb 2012</p>
<p class="news-text abs" style="left:730px;top:598px">Lorem Ipsum is simply dummy text of the printing and typesetting industry.</p>
<div class="news-rule abs"></div>
<p class="news-date abs" style="left:730px;top:666px">29, Feb 2012</p>
<p class="news-text abs" style="left:730px;top:689px">Lorem Ipsum is simply dummy text of the printing and typesetting industry.</p>

<h2 class="section-title abs" style="left:80px;top:710px;font-size:25px">Our Projects</h2>

<div class="round-arrow abs" style="left:88px;top:830px"><svg width="30" height="30" viewBox="0 0 30 30"><path d="M21 15H9m5-5-5 5 5 5" fill="none" stroke="#fff" stroke-width="1.8"/></svg></div>
<div class="round-arrow abs" style="left:910px;top:830px"><svg width="30" height="30" viewBox="0 0 30 30"><path d="M9 15h12m-5-5 5 5-5 5" fill="none" stroke="#fff" stroke-width="1.8"/></svg></div>

<article class="project-card abs" style="left:136px">
  <div class="project-photo" role="img" aria-label="Photo of a grassy field under trees" style="background:linear-gradient(#3d6a2a,#6d9a3c 55%,#a9c66a)"></div>
  <h3 class="project-title">LP PLAYER</h3>
  <p class="project-text">Field survey notes on local habitat, community partners and monitoring results from this season's work.</p>
</article>
<article class="project-card abs" style="left:328px">
  <div class="project-photo" role="img" aria-label="Photo of a large green tree in a meadow" style="background:linear-gradient(#a9c4dc,#3f7a2c 35%,#5f962f 75%,#8fb04a)"></div>
  <h3 class="project-title">VINTAGE CAMERA</h3>
  <p class="project-text">Field survey notes on local habitat, community partners and monitoring results from this season's work.</p>
</article>
<article class="project-card abs" style="left:521px">
  <div class="project-photo" role="img" aria-label="Photo of a coastline with green hills" style="background:linear-gradient(#b9d0e6,#dfe8f0 45%,#6f9aa8 62%,#5e8a98)"></div>
  <h3 class="project-title">VINTAGE CAMERA</h3>
  <p class="project-text">Field survey notes on local habitat, community partners and monitoring results from this season's work.</p>
</article>
<article class="project-card abs" style="left:716px">
  <div class="project-photo" role="img" aria-label="Photo of a field team working in a wetland" style="background:linear-gradient(#4a6e34,#2f4d24 50%,#5d6a44)"></div>
  <h3 class="project-title">VINTAGE CAMERA</h3>
  <p class="project-text">Field survey notes on local habitat, community partners and monitoring results from this season's work.</p>
</article>

<footer class="site-footer abs"></footer>
<h2 class="footer-title abs" style="left:55px;top:975px">Textual Content</h2>
<p class="footer-text abs">Lorem ipsum dolor sit amet, consectetur adipiscing elit. Integer id accumsan massa. Donec suscipit commodo velit. Fusce pharetra mi sit amet felis auctor tempor. Donec vel odio enim, id ultricies odio.</p>

<h2 class="footer-title abs" style="left:391px;top:975px">Browse</h2>
<ul class="footer-links abs">
  <li>Home</li><li>Services</li><li>Portfolio</li><li>Products</li><li>Blog</li><li>Contact Us</li>
</ul>

<h2 class="footer-title abs" style="left:532px;top:975px">Connect Us</h2>
<span class="social abs" style="left:530px;top:1023px"></span>
<span class="social abs" style="left:582px;top:1023px"></span>
<span class="social abs" style="left:530px;top:1065px"></span>
<span class="social abs" style="left:582px;top:1065px"><svg width="22" height="16" viewBox="0 0 22 16"><rect x="1" y="1" width="20" height="14" fill="#fff"/><path d="M1 1l10 8 10-8" fill="none" stroke="#050505" stroke-width="1.6"/></svg></span>

<h2 class="footer-title abs" style="left:724px;top:975px">Get In Touch With Us</h2>
<div class="field abs" style="top:1006px;height:21px">Your Name</div>
<div class="field abs" style="top:1037px;height:21px">Your Email</div>
<div class="field abs" style="top:1068px;height:68px;padding-top:6px">Your Message</div>
<div class="submit abs">Submit ::</div>

</body>
</html>
```